BRANDEMEIER & BRANDEMEIER,LLP NEEDS A NEW LETTERHEAD DESIGN

a conservative yet contemporary layout befitting a long established
firm, consistent with the times, some form of logo so it catches ones attention, and is
admirable, but portrays integrity
Updates

I would like to approve #22066987 Please advise how to do this as it’s confusing on the site so I can approve payment for the designer

Target Market(s)

real estate investors and building management people

Industry/Entity Type

Law Firm

Font styles to use
Serif

Colors

Designer to choose colors to be used in the design.

Requirements
Must have
• some form of conservative logo

```html
<!DOCTYPE html>
<html lang="en">
<head>
<meta charset="utf-8">
<title>Brandemeier LLP Letterhead</title>
<link rel="stylesheet" href="https://fonts.googleapis.com/css2?family=Cinzel:wght@400;500&family=Open+Sans:wght@400;600&family=Lato:wght@400;700&display=swap">
<style>
  :root {
    --navy: #143b66;
    --ink: #3a3a3a;
    --muted: #555555;
    --paper: #ffffff;
    --rule: rgba(255,255,255,0.35);
  }
  * { margin: 0; padding: 0; box-sizing: border-box; }
  html, body { width: 1040px; height: 1200px; overflow: hidden; background: var(--paper); }
  .letterhead {
    position: relative;
    width: 1040px;
    height: 1200px;
    background: var(--paper);
    font-family: "Open Sans", sans-serif;
    color: var(--ink);
  }
  .brand {
    position: absolute;
    left: 98px;
    top: 36px;
    display: flex;
    align-items: center;
    gap: 22px;
  }
  .brand-mark {
    width: 84px;
    height: 84px;
    background: var(--navy);
  }
  .brand-name {
    font-family: "Cinzel", serif;
    font-weight: 400;
    font-size: 40px;
    letter-spacing: 0.5px;
    color: var(--navy);
  }
  .sender {
    position: absolute;
    right: 102px;
    top: 48px;
    text-align: right;
  }
  .sender-name {
    font-family: "Cinzel", serif;
    font-weight: 500;
    font-size: 25px;
    color: var(--navy);
    line-height: 1;
  }
  .sender-title {
    font-family: "Lato", sans-serif;
    font-weight: 700;
    font-size: 19px;
    color: #222;
    margin-top: 2px;
  }
  .letter {
    position: absolute;
    left: 98px;
    top: 249px;
    width: 840px;
    font-size: 16.5px;
  }
  .issue-date { margin-bottom: 17px; }
  .recipient { line-height: 19px; margin-bottom: 47px; }
  .salutation { margin-bottom: 32px; }
  .body-text p {
    line-height: 27px;
    text-align: justify;
    hyphens: auto;
    -webkit-hyphens: auto;
    margin-bottom: 27px;
  }
  .closing { margin-top: 53px; }
  .signatory {
    margin-top: 56px;
    font-weight: 600;
    font-size: 20px;
    color: #333;
  }
  .signatory-title { margin-top: 5px; color: var(--muted); }
  .footer-band {
    position: absolute;
    left: 98px;
    right: 0;
    top: 1107px;
    height: 77px;
    background: var(--navy);
    color: #fff;
    font-family: "Lato", sans-serif;
    font-size: 19px;
    text-align: center;
    padding-right: 100px;
  }
  .footer-address { padding-top: 10px; padding-bottom: 6px; }
  .footer-contacts {
    display: inline-block;
    border-top: 1px solid var(--rule);
    padding: 5px 20px 0;
    word-spacing: 1px;
  }
  .footer-contacts .sep { margin: 0 20px; }
  .footer-disc {
    position: absolute;
    left: 4px;
    top: 1090px;
    width: 106px;
    height: 106px;
    border-radius: 50%;
    background: var(--navy);
    border: 4px solid var(--paper);
  }
</style>
</head>
<body>
<main class="letterhead">
  <header>
    <div class="brand">
      <div class="brand-mark"></div>
      <div class="brand-name">BRANDEMEIER,LLP</div>
    </div>
    <div class="sender">
      <div class="sender-name">DANIEL HARPER</div>
      <div class="sender-title">Managing director</div>
    </div>
  </header>

  <section class="letter">
    <p class="issue-date">Issuing Date: May 5, 2018</p>
    <p class="recipient">Name Of Employee Mr. XYZABC<br>Address of Employee<br>Address Line 2 etc..</p>
    <p class="salutation">Dear Mr.XYZABC</p>
    <div class="body-text">
      <p>Lorem Ipsum has been the industry's standard dummy text ever since the 1500s, when an unknown printer took a galley of type and scrambled it to make a type specimen book. It has survived not only five centuries, but also the leap into electronic typesetting, remaining essentially unchanged. It was popularised in the 1960s with the release of Marlowe Press sheets containing Lorem Ipsum passages, and more recently with desktop publishing software like Quillset Writer including versions of Lorem Ipsum.</p>
      <p>Lorem Ipsum is simply dummy text of the printing and typesetting industry. Lorem Ipsum has been the industry's standard dummy text ever since the 1500s, when an unknown printer took a galley of type and scrambled it to make a type specimen book.</p>
      <p>It has survived not only five centuries, but also the leap into electronic typesetting, remaining essentially unchanged. It was popularised in the 1960s with the release of Marlowe Press sheets containing Lorem IpsumIpsum passages.</p>
    </div>
    <p class="closing">Yours Sincerely</p>
    <p class="signatory">Daniel Harper</p>
    <p class="signatory-title">Managing Director</p>
  </section>

  <footer>
    <div class="footer-band">
      <div class="footer-address">Address goes here, Street line goes here,country code 12345</div>
      <div class="footer-contacts"><b>P:</b> 044-987 654 321<span class="sep">|</span><b>E:</b> info@brandemeierllp.com<span class="sep">|</span>www.brandemeierllp.com</div>
    </div>
    <div class="footer-disc"></div>
  </footer>
</main>
</body>
</html>
```